Kor'v Meridell Travel

We need a sleek, professional, inviting card to elicit global travel for the experienced and professional traveler. Royal blue, black and silver. (perhaps the wording could be silver with black shadow?-get creative) Maybe a watermark on the front and the full raised logo on the back.
We want a stylish and modern card, but professional.

```html
<!DOCTYPE html>
<html lang="en">
<head>
<meta charset="utf-8">
<title>Kor'v Meridell Travel — Business Card</title>
<link rel="stylesheet" href="https://fonts.googleapis.com/css2?family=Montserrat:wght@500;600;700&family=Arimo:wght@400&display=swap">
<style>
  :root {
    --bg: #0c0c0d;
    --card: #2a2b2d;
    --card-dark: #242527;
    --blue: #1ea6e3;
    --green: #7cc242;
    --white: #f2f2f2;
    --rule: #6a6b6e;
  }
  * { margin: 0; padding: 0; box-sizing: border-box; }
  html, body { width: 1200px; height: 820px; overflow: hidden; }
  body {
    background: var(--bg);
    display: flex;
    align-items: center;
    justify-content: center;
    gap: 50px;
    font-family: "Arimo", Arial, sans-serif;
  }
  .card {
    position: relative;
    width: 540px;
    height: 310px;
    background: var(--card);
    border-bottom: 4px solid var(--blue);
    border-left: 2px solid var(--blue);
    overflow: hidden;
  }
  .card--back { background: var(--card-dark); }

  .wordmark {
    position: absolute;
    font-family: "Montserrat", sans-serif;
    font-weight: 600;
    color: var(--blue);
    letter-spacing: 0.04em;
    text-align: center;
    line-height: 1.15;
  }
  .card--front .wordmark { top: 48px; right: 40px; font-size: 24px; }
  .card--back .wordmark {
    top: 50%; left: 50%;
    transform: translate(-50%, -50%);
    font-size: 30px;
  }
  .wordmark__sub {
    display: block;
    font-size: 0.62em;
    letter-spacing: 0.4em;
  }

  .divider {
    position: absolute;
    left: 230px; right: 40px; top: 150px;
    height: 1px;
    background: var(--rule);
  }

  .person { position: absolute; left: 40px; top: 128px; }
  .person__name {
    font-family: "Montserrat", sans-serif;
    font-weight: 700;
    font-size: 22px;
    color: var(--blue);
    letter-spacing: 0.02em;
  }
  .person__role {
    font-family: "Montserrat", sans-serif;
    font-weight: 500;
    font-size: 12px;
    color: var(--green);
    letter-spacing: 0.04em;
    margin-top: 2px;
  }

  .contacts {
    position: absolute;
    left: 40px; top: 190px;
    list-style: none;
  }
  .contacts li {
    display: flex;
    align-items: center;
    gap: 8px;
    font-size: 14px;
    color: var(--white);
    height: 22px;
  }
  .contacts svg { width: 16px; height: 16px; flex: none; }
  .contacts .accent { color: var(--blue); }

  .address {
    position: absolute;
    right: 40px; bottom: 60px;
    text-align: right;
    font-size: 13px;
    line-height: 1.45;
    color: var(--white);
  }
</style>
</head>
<body>

  <section class="card card--front" aria-label="Card front">
    <div class="wordmark">KOR'V MERIDELL<span class="wordmark__sub">TRAVEL</span></div>
    <div class="divider"></div>

    <div class="person">
      <div class="person__name">DORIAN VESK</div>
      <div class="person__role">MANAGING DIRECTOR</div>
    </div>

    <ul class="contacts">
      <li>
        <svg viewBox="0 0 16 16" aria-hidden="true"><rect width="16" height="16" rx="3" fill="#1ea6e3"/><path d="M5 4l2 2-1 1.2a6 6 0 0 0 2.8 2.8L10 9l2 2-1.2 1.2C7.5 12 4 8.5 3.8 5.2z" fill="#2a2b2d"/></svg>
        044-310 672 518
      </li>
      <li>
        <svg viewBox="0 0 16 16" aria-hidden="true"><rect width="16" height="16" rx="3" fill="#1ea6e3"/><rect x="5" y="3" width="6" height="10" rx="1" fill="none" stroke="#2a2b2d" stroke-width="1.5"/></svg>
        044-310 672 519
      </li>
      <li>
        <svg viewBox="0 0 16 16" aria-hidden="true"><rect width="16" height="16" rx="3" fill="#1ea6e3"/><rect x="3" y="4.5" width="10" height="7" fill="none" stroke="#2a2b2d" stroke-width="1.3"/><path d="M3 4.5l5 4 5-4" fill="none" stroke="#2a2b2d" stroke-width="1.3"/></svg>
        hello@korvmeridell.com
      </li>
      <li>
        <svg viewBox="0 0 16 16" aria-hidden="true"><rect width="16" height="16" rx="3" fill="#1ea6e3"/><circle cx="8" cy="8" r="4.5" fill="none" stroke="#2a2b2d" stroke-width="1.2"/><path d="M3.5 8h9M8 3.5c-2 2.5-2 6.5 0 9M8 3.5c2 2.5 2 6.5 0 9" fill="none" stroke="#2a2b2d" stroke-width="1"/></svg>
        <span>www.<span class="accent">korvmeridell</span>.com</span>
      </li>
    </ul>

    <address class="address">
      87, Calloway Harbour Road<br>
      30917, Estovia
    </address>
  </section>

  <section class="card card--back" aria-label="Card back">
    <div class="wordmark">KOR'V MERIDELL<span class="wordmark__sub">TRAVEL</span></div>
  </section>

</body>
</html>
```